Bright and beautiful business card for a coach

I'm a personal and business coach based in Perth, Australia. I need a business card that whilst subtle and elegant, will stand out and appeal on a table full of cards.

My business name is Fern Mentoring and the business card must represent the warmth and brightness implied in the name, without being gimmicky. It must have a warmth and appeal and be easy to read.

I prefer clean, minimalist designs.

It must align with the feel of my website and socials: https://www.fernmentoring-example.com.au/
https://www.instagram.com/fernmentoringau/
https://www.facebook.com/fernmentoringau
Updates

Hi Designers Thank you so much for taking the time to submit designs. I wonder if I could have explained myself a little better. Most of the designs that have been submitted look rather formal and many have quite corporate looking embellishments on them (to my eye). I would like softer, warmer, more organic. I’m open to people playing about and being more abstract, using softer embellishments (e.g the line drawing flowers and grasses I’ve used in my socials) incorporating other colours from my palette or like the social icons in my email signature (in PDF), perhaps playing with size/oversize, playing with the bleed. Please don’t be constrained by what I’ve already done, it merely needs to compliment. I’m sorry if I’m not using the right words or have led you astray. I’m no designer, but I’ve done my website, socials, email signature etc all myself (my logo was a design contest) and I was really hoping for my business card to be something more creative than I could have made with a template. Reminder: No black cards/sides please. Thank you 😊

Target Market(s)

Individuals, most likely but not all female. Creative thinkers. Likely professionals.

Industry/Entity Type

Business & Personal Coach

Contact Information for Business Card

(Fern Mentoring Logo) Name: Greta Pellham; Title: Business & Personal Coach; Phone number: +61 (0)458 913307; Email: greta@fernmentoring-example.com.au; Website: https://fernmentoring-example.com.au; Social icons for Facebook, Instagram & LinkedIn: @fernmentoringAU. Optional strapline: "A steady companion to help you find your own clear path"

Font styles to use
Sans Serif

Colors
00AB8E
00BBA5
67D7C9
C6EFE9
E9F9F6
59FF00
82FF00
B8FF75
E3FFCB
F4FFEA
FFC000
F8CF3A
FAE287
FDF2CF
FEFAEE

Requirements
Must have
• Must align with feel of my website and socials. Must have a pop of #FFC000 (possibly whole of one side, or at least a block). Bright or white background. Easy to read.
Nice to have
• Possibly incorporate the sunshine/grass picture I have used in website and socials - will upload.
Should not have
• Must not be black or dark. Not impersonal or corporate looking.

```html
<!DOCTYPE html>
<html lang="en">
<head>
<meta charset="utf-8">
<title>Fern Mentoring – Business Card</title>
<link href="https://fonts.googleapis.com/css2?family=Lato:wght@400;700&family=Allura&display=swap" rel="stylesheet">
<style>
  :root {
    --sun: #FFC000;
    --sun-soft: #F8CF3A;
    --sun-pale: #FAE287;
    --teal-soft: #67D7C9;
    --white: #FFFFFF;
    --stage: #D4D6D7;
    --grass-dark: #3E5A1E;
    --grass-mid: #6E8F2C;
    --grass-light: #A9B95A;
    --glow: #F3D9A8;
  }
  html, body {
    margin: 0;
    padding: 0;
    width: 1200px;
    height: 928px;
    overflow: hidden;
    background: var(--stage);
    font-family: "Lato", sans-serif;
  }
  .canvas {
    position: relative;
    width: 1200px;
    height: 928px;
  }
  .card {
    position: absolute;
    width: 620px;
    height: 360px;
    border-radius: 26px;
    overflow: hidden;
    box-shadow: 0 10px 24px rgba(0,0,0,0.18);
  }

  /* Front */
  .card--front {
    left: 110px;
    top: 60px;
    background: var(--sun);
  }
  .front-disc {
    position: absolute;
    left: 50%;
    top: 50%;
    width: 250px;
    height: 250px;
    margin: -125px 0 0 -125px;
    border-radius: 50%;
    background: var(--white);
    display: flex;
    align-items: center;
    justify-content: center;
  }
  .brand-name {
    font-family: "Lato", sans-serif;
    font-weight: 700;
    letter-spacing: 0.12em;
    text-transform: uppercase;
    color: var(--sun);
    text-align: center;
    line-height: 1.25;
  }
  .front-disc .brand-name {
    font-size: 24px;
  }

  /* Back */
  .card--back {
    left: 470px;
    top: 505px;
  }
  .back-photo {
    position: absolute;
    inset: 0;
    background:
      radial-gradient(circle at 52% 18%, var(--glow) 0%, rgba(243,217,168,0.5) 14%, rgba(243,217,168,0) 38%),
      linear-gradient(175deg, var(--grass-light) 0%, var(--grass-mid) 42%, var(--grass-dark) 100%);
  }
  .back-content {
    position: absolute;
    inset: 0;
    color: var(--white);
  }
  .back-brand {
    position: absolute;
    right: 40px;
    top: 92px;
    font-size: 22px;
  }
  .person {
    position: absolute;
    left: 34px;
    top: 88px;
  }
  .person-name {
    font-family: "Allura", cursive;
    font-size: 50px;
    line-height: 1;
    margin: 0;
    font-weight: 400;
  }
  .person-title {
    font-size: 15px;
    margin: 6px 0 0 4px;
  }
  .contact-list {
    position: absolute;
    left: 38px;
    top: 196px;
    margin: 0;
    padding: 0;
    list-style: none;
    font-size: 15px;
    line-height: 1.55;
  }
  .social-row {
    display: flex;
    align-items: center;
    gap: 6px;
  }
  .social-dot {
    width: 17px;
    height: 17px;
    border-radius: 4px;
  }
  .social-dot--a { background: var(--sun-soft); }
  .social-dot--b { background: var(--sun-pale); }
  .social-dot--c { background: var(--teal-soft); }
  .social-handle { margin-left: 4px; }
  .strapline {
    position: absolute;
    left: 38px;
    bottom: 26px;
    margin: 0;
    font-size: 16px;
    font-weight: 700;
    color: var(--sun);
  }
</style>
</head>
<body>
<main class="canvas">

  <section class="card card--front" aria-label="Card front">
    <div class="front-disc">
      <div class="brand-name">Fern<br>Mentoring</div>
    </div>
  </section>

  <section class="card card--back" aria-label="Card back">
    <div class="back-photo" role="img" aria-label="Sunlit grass meadow photograph with warm sun glow"></div>
    <div class="back-content">
      <div class="brand-name back-brand">Fern Mentoring</div>
      <div class="person">
        <h1 class="person-name">Greta Pellham</h1>
        <p class="person-title">Business &amp; Personal Coach</p>
      </div>
      <ul class="contact-list">
        <li>+61 (0)458 913307</li>
        <li>greta@fernmentoring-example.com.au</li>
        <li>www.fernmentoring-example.com.au</li>
        <li class="social-row">
          <span class="social-dot social-dot--a"></span>
          <span class="social-dot social-dot--b"></span>
          <span class="social-dot social-dot--c"></span>
          <span class="social-handle">@fernmentoringAU</span>
        </li>
      </ul>
      <p class="strapline">A steady companion to help you find your own clear path</p>
    </div>
  </section>

</main>
</body>
</html>
```